Telecommunications/Power civil contractor needs business card design

Were a new telecommunications/power underground civil contractor that is looking for a new business card design. Our company colours are silver or grey and orange. Feel free to use the white background logo or the black background logo.

Target Market(s)

Local contractors, utility companies, private sector mining/energy companies, developers.

Industry/Entity Type

Telecommunications

Contact Information for Business Card

Each card will need the following info:
Persons name:
Title:
E-mail:
Phone number:
Shop Address:
Mailing Address:

Requirements
Must have
• Each card will need the following info:
• Persons name:
• Title:
• E-mail:
• Phone number:
• Shop Address:
• Mailing Address:

```html
<!DOCTYPE html>
<html lang="en">
<head>
<meta charset="utf-8">
<title>Ridgeway Conduit Inc – Business Card</title>
<link rel="stylesheet" href="https://fonts.googleapis.com/css2?family=Source+Sans+3:wght@400;600;700;800&display=swap">
<style>
  :root {
    --orange: #f05a28;
    --grey: #5a5a5c;
    --ink: #2b2b2b;
    --white: #ffffff;
    --bg-top: #2c2c2c;
    --bg-bottom: #080808;
  }
  * { margin: 0; padding: 0; box-sizing: border-box; }
  html, body { width: 1200px; height: 900px; overflow: hidden; }
  body {
    position: relative;
    background: linear-gradient(180deg, var(--bg-top) 0%, #161616 55%, var(--bg-bottom) 100%);
    font-family: "Source Sans 3", "Myriad Pro", Arial, sans-serif;
  }
  .card {
    position: absolute;
    top: 306px;
    width: 440px;
    height: 271px;
    border-radius: 11px;
    overflow: hidden;
  }
  .card--front { left: 149px; background: var(--white); }
  .card--back { left: 608px; background: var(--orange); }

  /* front: brand block */
  .brand-mark {
    position: absolute;
    left: 78px; top: 56px;
    width: 86px; height: 86px;
    border-radius: 50%;
    background: var(--orange);
  }
  .brand-name {
    position: absolute;
    left: 0; width: 240px;
    text-align: center;
    font-weight: 800;
    color: var(--orange);
    line-height: 1;
  }
  .card--front .brand-name--main { top: 168px; font-size: 28px; letter-spacing: 1px; }
  .card--front .brand-name--sub { top: 198px; font-size: 13px; letter-spacing: 1.6px; }

  /* front: details */
  .details {
    position: absolute;
    left: 242px; top: 39px;
    color: var(--ink);
    font-size: 12.5px;
    line-height: 16px;
  }
  .person-name { font-size: 15.5px; font-weight: 600; color: var(--grey); line-height: 18px; }
  .person-name .first { color: var(--orange); }
  .person-title { font-size: 12.5px; margin-bottom: 12px; }
  .contact-line { display: flex; align-items: center; gap: 5px; }
  .contact-line svg { width: 9px; height: 9px; fill: var(--orange); flex: none; }
  .contacts { margin-bottom: 14px; }
  .address-label { color: var(--orange); font-weight: 700; }
  .address { margin-bottom: 6px; }

  /* back */
  .back-band {
    position: absolute;
    left: 0; top: 59px;
    width: 100%; height: 73px;
    background: var(--white);
  }
  .back-mark {
    position: absolute;
    left: 168px; top: 39px;
    width: 104px; height: 104px;
    border-radius: 50%;
    background: var(--orange);
    border: 6px solid var(--white);
  }
  .card--back .brand-name { width: 440px; color: var(--white); }
  .card--back .brand-name--main { top: 167px; font-size: 30px; letter-spacing: 1.5px; }
  .card--back .brand-name--sub { top: 199px; font-size: 14px; letter-spacing: 2px; }
</style>
</head>
<body>
  <section class="card card--front" aria-label="Business card front">
    <div class="brand-mark"></div>
    <div class="brand-name brand-name--main">RIDGEWAY</div>
    <div class="brand-name brand-name--sub">CONDUIT INC</div>

    <div class="details">
      <p class="person-name"><span class="first">Daniel</span> Harper</p>
      <p class="person-title">Managing Director</p>
      <div class="contacts">
        <p class="contact-line">
          <svg viewBox="0 0 10 10" aria-hidden="true"><path d="M1 3.2C1 2 2.2 1.5 5 1.5S9 2 9 3.2L7.6 4.1 6.8 3H3.2L2.4 4.1Z M2.6 5 3.6 3.8H6.4L7.4 5V8.5H2.6Z"/></svg>
          044-555 010 246
        </p>
        <p class="contact-line">
          <svg viewBox="0 0 10 10" aria-hidden="true"><path d="M0.5 2H9.5V8H0.5Z M1 2.4 5 5.5 9 2.4" stroke="#fff" stroke-width="0.7"/></svg>
          mail@ridgeway.com
        </p>
      </div>
      <p class="address-label">Shop Address:</p>
      <p class="address">12345, Address Goes Here<br>Country Name, 123456.</p>
      <p class="address-label">Mailing Address:</p>
      <p class="address">12345, Address Goes Here<br>Country Name, 123456.</p>
    </div>
  </section>

  <section class="card card--back" aria-label="Business card back">
    <div class="back-band"></div>
    <div class="back-mark"></div>
    <div class="brand-name brand-name--main">RIDGEWAY</div>
    <div class="brand-name brand-name--sub">CONDUIT INC</div>
  </section>
</body>
</html>
```